A layout of a webpage for oil trade platform

I would like to have a desgin of one page webpage (with section scrollling dowin) that woulf present the new product i.e. oil trade platform for wholesale buyers and sellers.
Layout should consist of the sections similar to the given at: https://porada.leczmypol.pl/panel-planowania-spotkan
However oil industy require more colors and more photo stories than here for doctor.
I. I woul imagine at first below menu a slider with brueg information about the product and its advantages with "more" button next to the prict screen of our platform on different displays (PC and mobile).
II. Bellow the slider I would imagine icons correspoing to the advantages of that plaftorm:
1. Purchase/sale process automation 24/7
2. Access to the best deals
3. Electronic offerings and orderings
4. Transaction status monitoring
5. Data and transaction security
II A) (optional):
In near future we would like to prepare a short video presenation. Hence please prepare a place to display that element here.
At the moment alternatvily please prepare a How it works section that would explan the platform operating process
III. Next secion is about benefits for Oil Purchaser
It can be done either by icons of by text and corresponding grahip for while section.
Benefits:
- Access to cheaper oil
- Convenience of online orders
- Possibility to compare prices on the market
- Transaction history
- Order status monitoring
- Seccurity and transparency of purchase
IV. Next seciont is about benefits for Oil Seller
Benefits:
- New sale channel
- Attracting new clients
- More oil sold
- Transaction security
- Possibility to integrate with distribution infrastructure and logistits for more efficient automation.
V. Contact form
VI. Footer
I would need a layout that that will correspond to the very dynamic logo but I would expect also a clean form, smoth and modern. It has to be proffessional layout with more corporate character.
It can use a paralax features if needed.

```html
<!DOCTYPE html>
<html lang="en">
<head>
<meta charset="utf-8">
<title>Crudeway – Oil Trade Platform</title>
<link href="https://fonts.googleapis.com/css2?family=Lato:wght@400;700;900&display=swap" rel="stylesheet">
<style>
:root{
  --navy:#152c5e;
  --navy-deep:#0f214a;
  --ink:#1b2a4c;
  --text:#555c66;
  --muted:#8a9099;
  --orange:#f05a24;
  --orange-light:#f7893a;
  --grey-bg:#f4f4f5;
  --line:#dcdde0;
  --white:#ffffff;
}
*{box-sizing:border-box;margin:0;padding:0}
html,body{width:1200px;height:3285px;overflow:hidden}
body{font-family:"Lato",sans-serif;color:var(--text);background:var(--white);position:relative}
section,header,footer{position:absolute;left:0;width:1200px}
.abs{position:absolute}
a{text-decoration:none}
.btn{position:absolute;display:flex;align-items:center;justify-content:center;gap:10px;color:var(--white);font-weight:700;font-size:16px;letter-spacing:.5px;background:linear-gradient(180deg,var(--orange-light),var(--orange));border-radius:3px;text-decoration:none}

/* hero */
.hero{top:0;height:668px;background:radial-gradient(ellipse at 70% 40%,#1f4590 0%,var(--navy) 55%,var(--navy-deep) 100%)}
.brand{display:flex;align-items:center;gap:12px;color:var(--white);font-weight:700;font-size:30px;letter-spacing:.5px}
.brand-dot{width:30px;height:30px;border-radius:50%;background:var(--orange)}
.nav{position:absolute;top:46px;left:415px;display:flex}
.nav a{display:block;padding:0 16px;height:36px;line-height:36px;font-size:13px;font-weight:700;color:var(--white);letter-spacing:.3px}
.nav a.active{background:var(--orange);margin-right:14px}
.hero h1{left:75px;top:250px;width:480px;font-size:33px;line-height:40px;font-weight:700;color:var(--white)}
.hero p{left:75px;top:345px;width:445px;font-size:17px;line-height:26px;color:#dfe6f4}
.devices{left:590px;top:180px;width:610px;height:488px;border-radius:6px 0 0 0;background:linear-gradient(135deg,#2a2f3a 0%,#3c4454 45%,#c9ced8 100%);opacity:.9}

/* features */
.features{top:668px;height:194px;background:var(--white)}
.feature{position:absolute;top:32px;width:180px;text-align:center}
.feature svg{display:block;margin:0 auto 14px}
.feature span{font-size:15px;line-height:21px;color:var(--ink);font-weight:700}

/* how */
.how{top:862px;height:426px;background:var(--grey-bg)}
.tablet{left:75px;top:43px;width:482px;height:340px;border-radius:14px;background:#2d3340}
.tablet-screen{left:25px;top:16px;width:420px;height:308px;background:linear-gradient(180deg,#e8ecef 0%,#9fc08c 45%,#5e86b3 60%,#f4f5f7 62%,#e6e8eb 100%)}
.tablet-cam{left:453px;top:160px;width:20px;height:20px;border-radius:50%;background:var(--white)}
.play{left:200px;top:130px}
h2{font-size:27px;font-weight:700;color:var(--ink)}
.how h2{left:612px;top:82px}
.how p{left:612px;top:132px;width:515px;font-size:14px;line-height:25px;color:var(--muted)}

/* benefits */
.buyer{top:1288px;height:527px;background:var(--white)}
.seller{top:1815px;height:528px;background:var(--grey-bg)}
.photo{top:0;height:100%}
.buyer .photo{left:613px;width:587px;background:linear-gradient(160deg,#9bc3e6 0%,#c8dbe8 45%,#5b5850 80%,#2e2d2e 100%)}
.seller .photo{left:0;width:587px;background:linear-gradient(200deg,#d9e2e8 0%,#b9c6cc 45%,#6b5b4a 80%,#3a322c 100%)}
.buyer h2{left:75px;top:62px}
.seller h2{left:634px;top:70px}
.benefits{list-style:none}
.buyer .benefits{left:75px;top:135px;width:500px}
.seller .benefits{left:634px;top:140px;width:430px}
.benefits li{display:flex;align-items:flex-start;gap:28px;min-height:60px;font-size:14.5px;font-weight:700;line-height:23px;color:#4a505a}
.benefits svg{flex:none;margin-top:-2px}

/* contact */
.contact{top:2343px;height:507px;background:var(--white);text-align:center}
.contact h2{position:absolute;left:0;width:1200px;top:70px}
.contact .lead{position:absolute;left:0;width:1200px;top:125px;font-size:14px;color:#666}
.field{position:absolute;border:1px solid var(--line);font-size:13px;color:#555;text-align:left;padding:0 14px;line-height:44px;height:46px;width:420px;left:165px}
.field.msg{left:613px;top:190px;width:422px;height:157px;line-height:40px}

/* footer */
.footer{top:2850px;height:435px;background:var(--grey-bg)}
.footer .brand{left:75px;top:50px;color:var(--ink);font-size:26px;position:absolute}
.address{left:75px;top:125px;font-size:15px;line-height:26px;color:#666;width:220px}
.contact-line{left:75px;display:flex;align-items:center;gap:18px;font-size:15px;color:var(--orange)}
.socials{left:75px;top:282px;display:flex;gap:18px}
.socials span{width:16px;height:16px;border-radius:3px;background:#9a9ea6}
.col h4{font-size:14px;font-weight:700;color:var(--ink);letter-spacing:.3px;margin-bottom:14px}
.col a{display:block;font-size:14.5px;line-height:30.5px;color:#666}
.news-input{left:883px;top:88px;width:242px;height:42px;border:1px solid var(--line);background:var(--white);font-size:13px;color:#777;line-height:40px;padding-left:12px}
.divider{left:75px;top:336px;width:1050px;height:1px;background:var(--line)}
.copy{left:0;width:1200px;top:378px;text-align:center;font-size:12px;color:#999}
</style>
</head>
<body>

<header class="hero">
  <div class="brand abs" style="left:75px;top:40px"><span class="brand-dot"></span>Crudeway</div>
  <nav class="nav">
    <a class="active" href="#">HOME</a><a href="#">ABOUT US</a><a href="#">SERVICES</a><a href="#">HOW IT WORKS</a><a href="#">BENEFITS</a><a href="#">BLOG</a><a href="#">CONTACT US</a>
  </nav>
  <h1 class="abs">Nam fermentum vestibulum amet turpis tincidunt.</h1>
  <p class="abs">Aliquam molestie, mi et imperdiet euismod, dui purus auctor tellus, et interdum lacus lectus et ante dignissim lectus vitae.</p>
  <a class="btn" href="#" style="left:75px;top:455px;width:150px;height:52px">MORE
    <svg width="10" height="14" viewBox="0 0 10 14"><path d="M2 1l6 6-6 6" stroke="#fff" stroke-width="2.6" fill="none"/></svg></a>
  <div class="devices abs" role="img" aria-label="Platform screens shown on desktop, laptop, tablet and phone"></div>
</header>

<section class="features">
  <div class="feature" style="left:95px">
    <svg width="60" height="60" viewBox="0 0 60 60" fill="none" stroke="#2b4a86" stroke-width="2.4"><circle cx="30" cy="30" r="26"/><circle cx="30" cy="30" r="16"/><path d="M30 20v10h8"/></svg>
    <span>Purchase/sale process automation 24/7</span></div>
  <div class="feature" style="left:300px">
    <svg width="60" height="60" viewBox="0 0 60 60" fill="none" stroke="#2b4a86" stroke-width="2.4"><rect x="6" y="28" width="10" height="24"/><path d="M16 30l10-12 4-12c5 0 6 5 5 10l-2 8h16c3 0 5 3 4 6l-5 18c-1 3-3 4-6 4H16"/></svg>
    <span>Access to the best deals</span></div>
  <div class="feature" style="left:510px">
    <svg width="60" height="60" viewBox="0 0 60 60" fill="none" stroke="#2b4a86" stroke-width="2.4"><rect x="4" y="4" width="52" height="52" rx="12"/><path d="M18 42l4-10 18-18 6 6-18 18z M18 42l10-4"/></svg>
    <span>Electronic offerings and orderings</span></div>
  <div class="feature" style="left:720px">
    <svg width="70" height="60" viewBox="0 0 70 60" fill="none" stroke="#2b4a86" stroke-width="2.4"><rect x="12" y="10" width="46" height="32" rx="2"/><path d="M4 46h62l-4 6H8z"/></svg>
    <span>Transaction status monitoring</span></div>
  <div class="feature" style="left:930px">
    <svg width="60" height="60" viewBox="0 0 60 60" fill="none" stroke="#2b4a86" stroke-width="2.4"><path d="M10 6h40v24c0 14-10 22-20 26C20 52 10 44 10 30z"/><path d="M30 6v50"/></svg>
    <span>Data and transaction security</span></div>
</section>

<section class="how">
  <div class="tablet abs">
    <div class="tablet-screen abs" role="img" aria-label="Video preview of the platform dashboard with sales chart"></div>
    <div class="tablet-cam abs"></div>
    <svg class="play abs" width="64" height="64" viewBox="0 0 64 64"><circle cx="32" cy="32" r="28" fill="none" stroke="#fff" stroke-width="5"/><path d="M26 19l20 13-20 13z" fill="#fff"/></svg>
  </div>
  <h2 class="abs">How it Works</h2>
  <p class="abs">Aliquam molestie, mi et imperdiet euismod, dui purus auctor tellus, et interdum lacus lectus et ante. Sed accumsan sollicitudin sapien, sit amet adipiscing turpis gravida ac. In congue, neque ac lobortis volutpat, libero mauris varius mi, vitae suscipit ipsum ligula vitae risus.</p>
  <a class="btn" href="#" style="left:612px;top:281px;width:245px;height:56px;font-size:14px">SEE HOW IT WORKS</a>
</section>

<section class="buyer">
  <h2 class="abs">Benefits for Oil Purchaser</h2>
  <ul class="benefits abs">
    <li><svg width="26" height="26" viewBox="0 0 26 26" fill="none" stroke="#f05a24" stroke-width="2.4"><circle cx="8" cy="8" r="6"/><path d="M12 12l12 12M18 18l-3 3M21 21l-3 3"/></svg>Access to cheaper oil</li>
    <li><svg width="26" height="26" viewBox="0 0 26 26" fill="none" stroke="#f05a24" stroke-width="2.4"><rect x="2" y="4" width="20" height="20" rx="2"/><path d="M9 17l2-5 11-11 3 3-11 11z"/></svg>Convenience of online orders</li>
    <li><svg width="26" height="26" viewBox="0 0 26 26" fill="none" stroke="#f05a24" stroke-width="2.6"><path d="M2 8h20M17 3l5 5-5 5M24 18H4M9 13l-5 5 5 5"/></svg>Possibility to compare prices on the market</li>
    <li><svg width="26" height="26" viewBox="0 0 26 26" fill="none" stroke="#f05a24" stroke-width="2.4"><circle cx="13" cy="13" r="11"/><path d="M13 7v6h5"/></svg>Transaction history</li>
    <li><svg width="26" height="26" viewBox="0 0 26 26" fill="none" stroke="#f05a24" stroke-width="2.2"><rect x="4" y="5" width="18" height="12"/><path d="M1 20h24"/></svg>Order status monitoring</li>
    <li><svg width="26" height="26" viewBox="0 0 26 26"><path d="M4 2h18v11c0 6-4 10-9 12C8 23 4 19 4 13z" fill="none" stroke="#f05a24" stroke-width="2.4"/><path d="M4 2h9v23C8 23 4 19 4 13z" fill="#f05a24"/></svg>Security and transparency of purchase</li>
  </ul>
  <div class="photo abs" role="img" aria-label="Photo of an oil engineer in a hard hat at an oil field"></div>
</section>

<section class="seller">
  <div class="photo abs" role="img" aria-label="Photo of an oil field worker using a laptop near pump jacks"></div>
  <h2 class="abs">Benefits for Oil Seller</h2>
  <ul class="benefits abs">
    <li><svg width="26" height="26" viewBox="0 0 26 26" fill="#f05a24"><rect x="9" y="1" width="8" height="7"/><rect x="1" y="18" width="7" height="7"/><rect x="9.5" y="18" width="7" height="7"/><rect x="18" y="18" width="7" height="7"/><path d="M12 8h2v4h8v6h-2v-4h-6v4h-2v-4H6v4H4v-6h8z"/></svg>New sale channel</li>
    <li><svg width="26" height="26" viewBox="0 0 26 26" fill="#f05a24"><circle cx="13" cy="7" r="5"/><circle cx="4.5" cy="10" r="3.5"/><circle cx="21.5" cy="10" r="3.5"/><path d="M5 24c0-6 4-10 8-10s8 4 8 10zM0 22c0-4 2-7 5-7l1 1c-2 2-3 4-3 6zM26 22c0-4-2-7-5-7l-1 1c2 2 3 4 3 6z"/></svg>Attracting new clients</li>
    <li><svg width="26" height="26" viewBox="0 0 26 26" fill="#f05a24"><path d="M13 1C9 8 5 12 5 17a8 8 0 0016 0c0-5-4-9-8-16z"/></svg>More oil sold</li>
    <li><svg width="26" height="26" viewBox="0 0 26 26" fill="#f05a24"><path d="M7 11V8a6 6 0 0112 0v3h-3V8a3 3 0 00-6 0v3z"/><rect x="4" y="11" width="18" height="14" rx="2"/></svg>Transaction security</li>
    <li><svg width="26" height="26" viewBox="0 0 26 26" fill="none" stroke="#f05a24" stroke-width="3"><circle cx="9" cy="10" r="5" stroke-dasharray="3 2"/><circle cx="19" cy="19" r="4" stroke-dasharray="2.5 1.5"/></svg>Possibility to integrate with distribution infrastructure and logistits for more efficient automation.</li>
  </ul>
</section>

<section class="contact">
  <h2>Contact Us</h2>
  <p class="lead">Vestibulum vel metus sit amet turpis bibendum tincidunt vel sit amet quam</p>
  <div class="field" style="top:190px">Name</div>
  <div class="field" style="top:245px">Email Address</div>
  <div class="field" style="top:300px">Phone No</div>
  <div class="field msg">Message</div>
  <a class="btn" href="#" style="left:480px;top:385px;width:240px;height:56px;font-size:14px">SUBMIT</a>
</section>

<footer class="footer">
  <div class="brand"><span class="brand-dot"></span>Crudeway</div>
  <p class="address abs">412 Harbour Lane,<br>Aberdeen, AB11 5QR</p>
  <div class="contact-line abs" style="top:200px">
    <svg width="14" height="11" viewBox="0 0 14 11" fill="#f05a24"><path d="M0 0h14v11H0z"/><path d="M0 0l7 6 7-6" stroke="#fff" stroke-width="1.4" fill="none"/></svg>hello@crudeway.example</div>
  <div class="contact-line abs" style="top:230px">
    <svg width="12" height="16" viewBox="0 0 12 16" fill="#f05a24"><path d="M6 0a6 6 0 00-6 6c0 4 6 10 6 10s6-6 6-10a6 6 0 00-6-6z"/><circle cx="6" cy="6" r="2" fill="#f3f3f3"/></svg>Map Location</div>
  <div class="socials abs"><span></span><span></span><span></span><span></span><span></span><span></span></div>

  <div class="col abs" style="left:378px;top:53px">
    <h4>SITE MAP</h4>
    <a href="#">Home</a><a href="#">About Us</a><a href="#">Services</a><a href="#">How it Works</a><a href="#">Benefits</a><a href="#">Blog</a><a href="#">Contact Us</a>
  </div>
  <div class="col abs" style="left:618px;top:53px">
    <h4>RESOURCES</h4>
    <a href="#">Aliquam molestie</a><a href="#">Perdiet euismod</a><a href="#">Dui purus auctor tellus</a><a href="#">Dum lacus lectus</a>
  </div>
  <div class="col abs" style="left:883px;top:53px"><h4>NEWSLETTER SIGN UP</h4></div>
  <div class="news-input abs">Enter Email Address</div>
  <a class="btn" href="#" style="left:1035px;top:140px;width:90px;height:42px;font-size:13px">SIGN UP</a>

  <div class="divider abs"></div>
  <p class="copy abs">Copyright © 2017. Company Name. All Right Reserved</p>
</footer>

</body>
</html>
```